Cyber Security Site Design (Products & Consulting)

I need my website redesigned to be engaging, clean, efficient and modern. My company (when its up and running) is going to be concentrated on two things: a few specific products for cyber security as well as cyber security consulting services. The background I bring to the field is having worked with small companies all the way to the largest government organizations and advising them on their security posture and how to improve it. We need the ability to add products and services easily.

For a sample product, you can use either Tarnet (http://www.tarnet-relay.org/) or Verodyne Ashmantle (https://www.verodyne.com/products/relay-hx-and-fortified-edge-portal).

It will replace https://lumerafieldworks.com/

Target Market(s)

Cyber Security professionals in all verticals

Coding

Coded - Design and coding required

Number of Pages Required

4 page

Font styles to use
Sans Serif

Colors
6b449b

Requirements
Must have
• Ability to easily modify
• Have main page
• Have product specific pages
• Have consulting services pages
• Have executive team information
• Clean, modern design
• Usage of the logo and its color scheme
Nice to have
• I like the idea of a left collapsed sidebar (so icons only) that can expand for text.
• I am also open to a very unique landing page, possibly a shape in the middle (hexagons maybe?) with each of the options there.
Should not have
• Nothing that looks like it came out of a hacker movie

```html
<!DOCTYPE html>
<html lang="en">
<head>
<meta charset="utf-8">
<title>Lumera Fieldworks – Site Design Board</title>
<link rel="stylesheet" href="https://fonts.googleapis.com/css2?family=Montserrat:wght@400;500;600;700&display=swap">
<style>
  :root {
    --board: #d5d5d5;
    --purple: #5b2a90;
    --brand: #6b449b;
    --purple-deep: #4a1f7d;
    --lavender: #b9a6d6;
    --ink: #2b2b33;
    --muted: #55555f;
    --soft: #f3f2f8;
    --line: #d9d9e2;
    --white: #ffffff;
    --footer: #161616;
  }
  * { box-sizing: border-box; margin: 0; padding: 0; }
  html, body { width: 1030px; height: 1200px; overflow: hidden; }
  body { background: var(--board); font-family: "Montserrat", sans-serif; color: var(--ink); position: relative; }
  .defs { position: absolute; width: 0; height: 0; }

  /* ---------- landing panels ---------- */
  .landing { position: absolute; left: 30px; width: 450px; height: 268px; overflow: hidden; box-shadow: 0 1px 4px rgba(0,0,0,.18); }
  .landing--dark { top: 54px; background: radial-gradient(circle at 60% 45%, #6c3aa3 0%, var(--purple) 55%, #4c1f80 100%); }
  .landing--light { top: 342px; background: linear-gradient(120deg, #f1ecec 0%, #eadede 40%, #d9c7c3 70%, #ece7ea 100%); }
  .landing__brand { position: absolute; left: 65px; top: 15px; display: flex; align-items: center; gap: 4px; font-weight: 600; font-size: 9px; white-space: nowrap; }
  .landing--dark .landing__brand { color: var(--white); }
  .landing--light .landing__brand { color: var(--purple-deep); }
  .brand-dot { width: 10px; height: 10px; border-radius: 50%; background: currentColor; flex: none; }
  .pill-outline { position: absolute; left: 351px; top: 13px; width: 35px; height: 13px; border-radius: 7px; font-size: 4.5px; font-weight: 600; display: flex; align-items: center; justify-content: center; }
  .landing--dark .pill-outline { border: 1px solid var(--white); color: var(--white); }
  .landing--light .pill-outline { border: 1px solid var(--purple); color: var(--purple); }
  .hex-cluster { position: absolute; left: 0; top: 0; }
  .landing__legal { position: absolute; left: 0; right: 0; top: 253px; text-align: center; font-size: 4.6px; }
  .landing--dark .landing__legal { color: rgba(255,255,255,.85); }
  .landing--light .landing__legal { color: var(--muted); }
  .hex-label { font-family: "Montserrat", sans-serif; font-size: 5.2px; font-weight: 600; fill: var(--white); text-anchor: middle; }
  .hex-center { font-family: "Montserrat", sans-serif; font-size: 8px; font-weight: 600; text-anchor: middle; }

  /* ---------- website page ---------- */
  .site { position: absolute; left: 498px; top: 54px; width: 450px; height: 1095px; background: var(--white); box-shadow: 0 1px 4px rgba(0,0,0,.18); overflow: hidden; }
  .site > * { position: absolute; }
  .header { left: 0; top: 0; width: 450px; height: 28px; background: var(--white); }
  .header__brand { position: absolute; left: 64px; top: 10px; display: flex; align-items: center; gap: 3px; font-weight: 600; font-size: 7px; color: var(--purple-deep); white-space: nowrap; }
  .brand-dot--sm { width: 8px; height: 8px; }
  .nav { position: absolute; left: 166px; top: 12px; display: flex; gap: 15px; font-size: 5.2px; font-weight: 500; color: var(--ink); list-style: none; white-space: nowrap; }
  .nav .is-active { color: var(--purple); font-weight: 600; }

  .hero { left: 0; top: 28px; width: 450px; height: 190px; }
  .hero__image { position: absolute; inset: 0; background: radial-gradient(circle at 62% 38%, #e8a46a 0%, #8a5b4a 8%, #2a3656 24%, #1a2540 55%, #0f1628 100%); }
  .hero__title { position: absolute; left: 242px; top: 61px; font-size: 14px; font-weight: 700; color: var(--white); white-space: nowrap; }
  .hero__btn { position: absolute; left: 341px; top: 85px; width: 44px; height: 13px; border: 1px solid var(--white); border-radius: 7px; color: var(--white); font-size: 4.6px; font-weight: 600; display: flex; align-items: center; justify-content: center; }
  .hero__dots { position: absolute; left: 193px; top: 172px; display: flex; gap: 2px; }
  .hero__dots span { width: 15px; height: 1.6px; background: var(--white); }
  .hero__dots span.is-dim { background: rgba(255,255,255,.4); }

  .about { left: 0; top: 218px; width: 450px; height: 176px; background: var(--soft); }
  .about__photo { position: absolute; left: 0; top: 0; width: 178px; height: 176px; background: linear-gradient(160deg, #eceaf0 0%, #d9d3d5 45%, #5a5a62 80%, #3a3a42 100%); }
  .about__title { position: absolute; left: 210px; top: 35px; width: 200px; font-size: 14px; font-weight: 700; line-height: 15px; color: var(--ink); }
  .about__title em { font-style: normal; color: var(--purple); }
  .about__text { position: absolute; left: 210px; top: 75px; width: 170px; font-size: 4.1px; line-height: 8.4px; color: var(--muted); }
  .btn { height: 11px; border-radius: 6px; background: var(--purple); color: var(--white); font-size: 4.4px; font-weight: 600; display: flex; align-items: center; justify-content: center; }
  .about__btn { position: absolute; left: 210px; top: 136px; width: 43px; }

  .section-title { left: 0; width: 450px; text-align: center; font-size: 14px; font-weight: 600; color: var(--ink); }
  .section-title em { font-style: normal; font-weight: 700; color: var(--purple); }
  .consulting-title { top: 436px; }
  .consulting-text { left: 125px; top: 464px; width: 200px; text-align: center; font-size: 4.1px; line-height: 8.4px; color: var(--muted); }
  .consulting-btn { left: 202px; top: 503px; width: 44px; }
  .consulting-visual { left: 100px; top: 522px; }

  .products-title { top: 714px; }
  .product { top: 743px; width: 100px; }
  .product--a { left: 65px; } .product--b { left: 174px; } .product--c { left: 284px; }
  .product__image { width: 99px; height: 61px; }
  .product--a .product__image { background: linear-gradient(135deg, #7d8ea6 0%, #2f3f5a 55%, #1b2433 100%); }
  .product--b .product__image { background: linear-gradient(135deg, #aab4c2 0%, #5e6878 50%, #2a3140 100%); }
  .product--c .product__image { background: radial-gradient(circle at 55% 50%, #c0704f 0%, #3a3f55 35%, #141a2a 100%); }
  .product__name { margin-top: 7px; font-size: 5.2px; font-weight: 700; color: var(--ink); }
  .product__text { margin-top: 5px; font-size: 4px; line-height: 8px; color: var(--muted); }
  .product__link { margin-top: 6px; font-size: 4.4px; font-weight: 600; color: var(--purple); }
  .diamond { width: 26px; height: 26px; background: #e4e4ea; transform: rotate(45deg); }
  .diamond--a { left: 55px; top: 760px; }
  .diamond--b { left: 360px; top: 734px; }

  .contact { left: 0; top: 912px; width: 450px; height: 150px; background: linear-gradient(100deg, #eceef5 0%, #f6f6fa 45%, #e8eaf2 100%); }
  .contact__title { position: absolute; left: 0; top: 21px; width: 450px; text-align: center; font-size: 14px; font-weight: 600; color: var(--ink); }
  .contact__title em { font-style: normal; font-weight: 700; color: var(--purple); }
  .contact__text { position: absolute; left: 105px; top: 40px; width: 240px; text-align: center; font-size: 4.2px; line-height: 8.4px; color: var(--muted); }
  .field { position: absolute; background: var(--white); border: 1px solid var(--line); font-size: 4.2px; line-height: 5px; color: var(--muted); padding: 2.5px 3px; }
  .field--name { left: 92px; top: 70px; width: 131px; height: 12px; }
  .field--phone { left: 92px; top: 85px; width: 131px; height: 12px; }
  .field--email { left: 92px; top: 100px; width: 131px; height: 12px; }
  .field--comments { left: 227px; top: 70px; width: 140px; height: 42px; }
  .contact__submit { position: absolute; left: 206px; top: 116px; width: 38px; height: 13px; border-radius: 7px; }

  .footer { left: 0; top: 1062px; width: 450px; height: 33px; background: var(--footer); color: var(--white); }
  .footer__nav { position: absolute; left: 65px; top: 10px; display: flex; gap: 9px; list-style: none; font-size: 4.4px; font-weight: 500; white-space: nowrap; }
  .footer__legal { position: absolute; left: 65px; top: 21px; font-size: 4.2px; color: #d0d0d0; }
  .footer__social { position: absolute; left: 342px; top: 12px; display: flex; gap: 2px; }
  .footer__social span { width: 10px; height: 10px; border: 1px solid var(--white); border-radius: 50%; }
</style>
</head>
<body>

<svg class="defs" aria-hidden="true">
  <defs>
    <polygon id="hex" points="34,0 17,29.4 -17,29.4 -34,0 -17,-29.4 17,-29.4"/>
    <g id="icon-doc" fill="#fff">
      <path d="M-5,-8 H2 L6,-4 V8 H-5 Z"/>
      <rect x="-3" y="-1" width="7" height="1.2" fill="#5b2a90"/>
      <rect x="-3" y="2" width="7" height="1.2" fill="#5b2a90"/>
      <rect x="-3" y="5" width="5" height="1.2" fill="#5b2a90"/>
    </g>
    <g id="icon-server" fill="#fff">
      <ellipse cx="0" cy="-5" rx="7" ry="4"/>
      <rect x="-5" y="-3" width="10" height="3" rx="1"/>
      <rect x="-5" y="1" width="10" height="3" rx="1"/>
      <rect x="-0.6" y="4" width="1.2" height="3"/>
      <rect x="-5" y="7" width="10" height="1.2"/>
    </g>
    <g id="icon-chat" fill="#fff">
      <ellipse cx="-2" cy="-2" rx="6" ry="4.5"/>
      <path d="M-5,1 L-7,5 L-2,2 Z"/>
      <ellipse cx="4" cy="2.5" rx="4.5" ry="3.5"/>
      <path d="M6,5 L8,8 L4,6 Z"/>
    </g>
    <g id="icon-people" fill="#fff">
      <circle cx="0" cy="-4" r="2.6"/>
      <circle cx="-6" cy="-2.5" r="2"/>
      <circle cx="6" cy="-2.5" r="2"/>
      <path d="M-4.5,5 A4.5,5 0 0 1 4.5,5 Z"/>
      <path d="M-10,5 A3.5,4 0 0 1 -3.5,3 L-4.5,5 Z"/>
      <path d="M10,5 A3.5,4 0 0 0 3.5,3 L4.5,5 Z"/>
    </g>
    <g id="icon-org" fill="#fff">
      <rect x="-2.5" y="-8" width="5" height="4"/>
      <rect x="-0.5" y="-4" width="1" height="3"/>
      <rect x="-7" y="-1.5" width="14" height="1"/>
      <rect x="-7" y="-1" width="1" height="3"/>
      <rect x="-0.5" y="-1" width="1" height="3"/>
      <rect x="6" y="-1" width="1" height="3"/>
      <rect x="-9" y="2" width="5" height="4"/>
      <rect x="-2.5" y="2" width="5" height="4"/>
      <rect x="4" y="2" width="5" height="4"/>
    </g>
    <g id="icon-lock" fill="none" stroke="#fff" stroke-width="1.3">
      <path d="M-4,-2 V-5 A4,4 0 0 1 4,-5 V-2"/>
      <rect x="-6" y="-2" width="12" height="10" rx="1"/>
      <circle cx="0" cy="2" r="1.3"/>
      <path d="M0,3.3 V6"/>
    </g>
  </defs>
</svg>

<!-- Landing: dark variant -->
<section class="landing landing--dark">
  <div class="landing__brand"><span class="brand-dot"></span>Lumera Fieldworks</div>
  <div class="pill-outline">Sign Up</div>
  <svg class="hex-cluster" width="450" height="268" viewBox="0 0 450 268">
    <g fill="none" stroke="#fff" stroke-width="1.8">
      <use href="#hex" x="226" y="74"/>
      <use href="#hex" x="172" y="106"/>
      <use href="#hex" x="280" y="106"/>
      <use href="#hex" x="172" y="169"/>
      <use href="#hex" x="280" y="169"/>
      <use href="#hex" x="226" y="201"/>
    </g>
    <use href="#icon-doc" x="226" y="66"/><text class="hex-label" x="226" y="92">Service 02</text>
    <use href="#icon-server" x="172" y="98"/><text class="hex-label" x="172" y="124">Service 01</text>
    <use href="#icon-chat" x="280" y="98"/><text class="hex-label" x="280" y="124">Service 03</text>
    <use href="#icon-people" x="172" y="161"/><text class="hex-label" x="172" y="187">Service 04</text>
    <use href="#icon-org" x="280" y="161"/><text class="hex-label" x="280" y="187">Service 05</text>
    <use href="#icon-lock" x="226" y="193"/><text class="hex-label" x="226" y="219">Service 06</text>
    <text class="hex-center" x="226" y="139" fill="#fff">Lumera</text>
  </svg>
  <p class="landing__legal">© 2018 All Rights Are Reserved.Terms of Use | Privacy Policy</p>
</section>

<!-- Landing: light photo variant -->
<section class="landing landing--light">
  <div role="img" aria-label="Soft focus photo of hands typing on a laptop with floating web icons" style="position:absolute;inset:0;"></div>
  <div class="landing__brand"><span class="brand-dot"></span>Lumera Fieldworks</div>
  <div class="pill-outline">Sign Up</div>
  <svg class="hex-cluster" width="450" height="268" viewBox="0 0 450 268">
    <g fill="#5b2a90" stroke="#fff" stroke-width="1.8">
      <use href="#hex" x="226" y="74"/>
      <use href="#hex" x="172" y="106"/>
      <use href="#hex" x="280" y="106"/>
      <use href="#hex" x="172" y="169"/>
      <use href="#hex" x="280" y="169"/>
      <use href="#hex" x="226" y="201"/>
    </g>
    <use href="#icon-doc" x="226" y="66"/><text class="hex-label" x="226" y="92">Service 02</text>
    <use href="#icon-server" x="172" y="98"/><text class="hex-label" x="172" y="124">Service 01</text>
    <use href="#icon-chat" x="280" y="98"/><text class="hex-label" x="280" y="124">Service 03</text>
    <use href="#icon-people" x="172" y="161"/><text class="hex-label" x="172" y="187">Service 04</text>
    <use href="#icon-org" x="280" y="161"/><text class="hex-label" x="280" y="187">Service 05</text>
    <use href="#icon-lock" x="226" y="193"/><text class="hex-label" x="226" y="219">Service 06</text>
    <text class="hex-center" x="226" y="139" fill="#4a1f7d">Lumera</text>
  </svg>
  <p class="landing__legal">© 2018 All Rights Are Reserved.Terms of Use | Privacy Policy</p>
</section>

<!-- Website home page -->
<main class="site">
  <header class="header">
    <div class="header__brand"><span class="brand-dot brand-dot--sm"></span>Lumera Fieldworks</div>
    <ul class="nav">
      <li class="is-active">Home</li><li>Products</li><li>Consulting</li><li>Executive Team</li><li>About</li><li>Contact</li>
    </ul>
  </header>

  <section class="hero">
    <div class="hero__image" role="img" aria-label="Dark blue technology photo of a hooded figure at a laptop with glowing interface graphics"></div>
    <h1 class="hero__title">Lumera Fieldworks</h1>
    <div class="hero__btn">Read More</div>
    <div class="hero__dots"><span></span><span></span><span class="is-dim"></span><span></span></div>
  </section>

  <section class="about">
    <div class="about__photo" role="img" aria-label="Portrait photo of the company founder in a dark blazer"></div>
    <h2 class="about__title">About <em>Daniel Moreau Halvorsen</em></h2>
    <p class="about__text">We guide teams from small firms to national agencies in measuring their security posture, closing gaps and building controls that hold up under audit. Our advice is practical, vendor neutral and shaped by decades of field work. Every engagement ends with a clear roadmap your staff can own and maintain.</p>
    <div class="btn about__btn">Read More</div>
  </section>

  <h2 class="section-title consulting-title">Our <em>Consulting</em></h2>
  <p class="consulting-text">Assessments, architecture reviews and incident readiness for organisations of every size. We review your environment, rank the risks that matter and help your people put lasting fixes in place without slowing the business down.</p>
  <div class="btn consulting-btn">Read More</div>
  <svg class="consulting-visual" width="250" height="160" viewBox="0 0 250 160">
    <polygon points="115,90 185,125 115,160 45,125" fill="#e2e2e8"/>
    <polygon points="40,4 10,86 38,86" fill="#b9a6d6"/>
    <polygon points="212,90 240,70 210,150" fill="#b9a6d6"/>
    <defs>
      <linearGradient id="consultingPhoto" x1="0" y1="0" x2="1" y2="1">
        <stop offset="0" stop-color="#e9e6ee"/>
        <stop offset=".5" stop-color="#c99a8c"/>
        <stop offset="1" stop-color="#6e6a78"/>
      </linearGradient>
    </defs>
    <polygon role="img" aria-label="Photo of hands using a phone above a laptop keyboard with security icons" points="50,4 250,4 227,124 20,124" fill="url(#consultingPhoto)"/>
  </svg>

  <h2 class="section-title products-title">Our <em>Products</em></h2>
  <div class="diamond diamond--a"></div>
  <div class="diamond diamond--b"></div>
  <article class="product product--a">
    <div class="product__image" role="img" aria-label="Photo of a person working at a laptop with cloud security graphics"></div>
    <h3 class="product__name">Tarnet Relay Gateway</h3>
    <p class="product__text">Hardened relay that filters and logs outbound traffic for every site.</p>
    <p class="product__link">Read More</p>
  </article>
  <article class="product product--b">
    <div class="product__image" role="img" aria-label="Photo of hands on a keyboard with a padlock graphic"></div>
    <h3 class="product__name">Ashmantle Edge Portal</h3>
    <p class="product__text">Secure web gateway with policy control and encrypted session inspection.</p>
    <p class="product__link">Read More</p>
  </article>
  <article class="product product--c">
    <div class="product__image" role="img" aria-label="Photo of a hand holding a phone with glowing network icons"></div>
    <h3 class="product__name">Verodyne Relay HX</h3>
    <p class="product__text">High throughput proxy appliance built for large agency networks.</p>
    <p class="product__link">Read More</p>
  </article>

  <section class="contact">
    <h2 class="contact__title">Contact <em>Us</em></h2>
    <p class="contact__text">Tell us about your environment and goals. A member of our team will reply within one business day to arrange a first call.</p>
    <div class="field field--name">Name:</div>
    <div class="field field--phone">Phone:</div>
    <div class="field field--email">Email:</div>
    <div class="field field--comments">Comments:</div>
    <div class="btn contact__submit">SUBMIT</div>
  </section>

  <footer class="footer">
    <ul class="footer__nav"><li>HOME</li><li>PRODUCTS</li><li>CONSULTING</li><li>EXECUTIVE TEAM</li><li>ABOUT</li><li>CONTACT</li></ul>
    <p class="footer__legal">© 2018 All Rights Are Reserved.Terms of Use | Privacy Policy</p>
    <div class="footer__social"><span></span><span></span><span></span><span></span></div>
  </footer>
</main>

</body>
</html>
```